Pemberlux: Smart Quotes for Wine Lovers

Hello. I am completing book of quotes for wine lovers. Need the text formatted so that it is easy to read and aesthetically pleasing...modern, clean, smart. Number the pages. The cover is complete. Book is small square. 7.5 by 7.5 inches. If you want to show me first few pages that would be awesome. Thank you!
Updates

I edited the quotes so if you downloaded first ones, please grab these ones instead, thank you! 

Target Market(s)

wine lovers. Urban. Modern.

Industry/Entity Type

Quotes

Requirements
Should not have
• No color. black and white only.

```html
<!DOCTYPE html>
<html lang="en">
<head>
<meta charset="utf-8">
<title>Pemberlux: Smart Quotes for Wine Lovers</title>
<link rel="stylesheet" href="https://fonts.googleapis.com/css2?family=Noto+Sans:wght@400;700&display=swap">
<style>
  :root {
    --page: #000000;
    --ink: #ffffff;
    --gutter: #5a5a5a;
  }
  html, body {
    margin: 0;
    padding: 0;
    width: 1200px;
    height: 600px;
    overflow: hidden;
    background: var(--page);
  }
  .spread {
    position: relative;
    width: 1200px;
    height: 600px;
    background: var(--page);
    color: var(--ink);
    font-family: "Noto Sans", sans-serif;
  }
  .gutter {
    position: absolute;
    left: 599px;
    top: 0;
    width: 1px;
    height: 600px;
    background: var(--gutter);
  }
  .page {
    position: absolute;
    top: 0;
    width: 600px;
    height: 600px;
  }
  .page--left { left: 0; }
  .page--right { left: 600px; }

  .quote {
    position: absolute;
    top: 204px;
    margin: 0;
    font-size: 39px;
    font-weight: 400;
    line-height: 50px;
    letter-spacing: 0.5px;
  }
  .page--left .quote {
    right: 141px;
    text-align: right;
  }
  .page--right .quote {
    left: 139px;
    text-align: left;
  }
  .attribution {
    position: absolute;
    margin: 0;
    font-size: 13px;
    letter-spacing: 1px;
    text-transform: uppercase;
  }
  .page--left .attribution {
    top: 420px;
    right: 141px;
  }
  .page--right .attribution {
    top: 371px;
    left: 139px;
  }
  .bio {
    position: absolute;
    top: 518px;
    margin: 0;
    font-size: 7.5px;
    font-weight: 700;
    line-height: 11px;
  }
  .page--left .bio {
    right: 141px;
    width: 290px;
    text-align: right;
  }
  .page--right .bio {
    left: 139px;
    width: 300px;
    text-align: left;
  }
</style>
</head>
<body>
  <main class="spread">
    <section class="page page--left">
      <p class="quote">The connoisseur<br>does not drink<br>wine but tastes<br>its secrets</p>
      <p class="attribution">—Mateo Varenne</p>
      <p class="bio">Mateo Andrés Varenne i Solà, 1st Marqués de Varenne de Solmont (1902–1981) Spanish Surrealist Painter.</p>
    </section>
    <div class="gutter"></div>
    <section class="page page--right">
      <p class="quote">Wine is the<br>divine juice of<br>September</p>
      <p class="attribution">—Orvel</p>
      <p class="bio">Henri-Lucien Castel&nbsp; known by his “nom de plume” Orvel.<br>(1692 –1776). French Enlightenment Writer, Historian and Philosopher.</p>
    </section>
  </main>
</body>
</html>
```